Desktop and Networking Support Course 9.17.25

Important the ad should not be very busy with the text taking up the major part of the ad .. please do not make the text so big that it takes up most of the ad..
Flyer Design Brief for Graphic Artist
also i am looking for something unique or creative that it will stand out .
Size & Layout:
Full Page with Bleed: 8” x 10.75” + 0.25” bleed on all sides.
Footer Space: Leave a 1-inch margin at the bottom for footer content (e.g., contact info, logo, or call-to-action).
Target Audience:
College-age students (around 24 years old)
Located in the USA
Interested in creative, professional, and career-building opportunities
Purpose:
To attract students to enroll in a college program
Flyer should be eye-catching, unique, and creative
Text must be clear and readable,
Design Style:
Use vector art, typography, or photography — your choice
If using photography, feature a white young professional USA citizen:
Wearing a white collared shirt
not with long hair
Creative Direction:
The flyer should stand out visually — something people would want to look at and keep
Showcase creativity and professionalism
Use bold colors, dynamic layout, or unexpected design elements to grab attention
Avoid clutter — keep the design balanced and clean
Text Suggestions (can be adjusted):
Footer,
please leave one inch on the bottom for the footer

```html
<!DOCTYPE html>
<html lang="en">
<head>
<meta charset="UTF-8">
<title>Desktop &amp; Network Support Course</title>
<link href="https://fonts.googleapis.com/css2?family=Outfit:wght@600;700&family=Didact+Gothic&display=swap" rel="stylesheet">
<style>
  :root {
    --navy: #0a4a6e;
    --navy-deep: #073c5b;
    --coral: #ec604a;
    --coral-card: #ea5e49;
    --sun: #fdc43c;
    --white: #ffffff;
    --photo-light: #e4e1dd;
    --photo-dark: #c9c4bf;
  }
  * { margin: 0; padding: 0; box-sizing: border-box; }
  html, body { width: 893px; height: 1200px; overflow: hidden; }
  body { background: var(--navy); }
  .flyer {
    position: relative; width: 893px; height: 1200px; overflow: hidden;
    background: linear-gradient(135deg, var(--navy-deep) 0%, var(--navy) 45%, var(--navy-deep) 100%);
    font-family: "Outfit", sans-serif; color: var(--white);
  }
  .backdrop { position: absolute; inset: 0; }
  .headline {
    position: absolute; left: 44px; top: 40px;
    font-weight: 700; font-size: 50px; line-height: 72px; letter-spacing: -1.5px;
  }
  .headline .accent { color: var(--coral); }
  .headline .second { display: block; padding-left: 6px; }
  .course-title {
    position: absolute; left: 43px; top: 201px;
    font-weight: 700; font-size: 33px; line-height: 57px; letter-spacing: -0.6px;
    color: var(--sun);
  }
  .checklist { position: absolute; left: 44px; top: 326px; list-style: none; }
  .checklist li {
    display: flex; align-items: center; height: 58px;
    font-family: "Didact Gothic", sans-serif; font-size: 26px; letter-spacing: 0.3px;
  }
  .checklist svg { width: 27px; height: 27px; margin-right: 22px; flex: none; }
  .highlights {
    position: absolute; left: 43px; top: 588px; list-style: none;
    font-weight: 700; font-size: 22.5px; letter-spacing: -0.6px;
  }
  .highlights li { height: 53px; line-height: 30px; }
  .card {
    position: absolute; width: 314px; height: 179px; border-radius: 16px;
    background: var(--coral-card); box-shadow: 0 4px 14px rgba(150, 40, 25, 0.18);
    padding: 22px 21px;
  }
  .card--modes { left: 120px; top: 882px; }
  .card--aid { left: 458px; top: 918px; }
  .card .icon { width: 48px; height: 48px; display: block; }
  .card p {
    margin-top: 18px; font-weight: 700; font-size: 23px; line-height: 39px; letter-spacing: -0.5px;
  }
</style>
</head>
<body>
<div class="flyer">
  <svg class="backdrop" width="893" height="1200" viewBox="0 0 893 1200">
    <defs>
      <linearGradient id="photoTone" x1="0" y1="0" x2="0" y2="1">
        <stop offset="0" stop-color="var(--photo-dark)"/>
        <stop offset="1" stop-color="var(--photo-light)"/>
      </linearGradient>
    </defs>
    <path class="portrait" d="M645,150 Q700,100 780,110 Q850,125 870,200 L893,230 L893,925 L528,925 L535,700 Q555,500 650,440 Z" fill="url(#photoTone)" role="img" aria-label="Smiling young professional in a white collared shirt"/>
    <g fill="none" stroke="#ffffff" stroke-width="2.5" stroke-linejoin="miter">
      <polyline class="zigzag" points="666,52 673,58 681,51 689,58 697,51 705,58 713,51 721,58 731,52"/>
      <polyline class="zigzag" points="38,795 45,801 53,794 61,801 69,794 77,801 85,794 93,801 103,795"/>
    </g>
    <g class="dot-grid" fill="#ffffff" opacity="0.55">
      <circle cx="573" cy="341" r="1.3"/><circle cx="591" cy="341" r="1.3"/><circle cx="609" cy="341" r="1.3"/><circle cx="627" cy="341" r="1.3"/>
      <circle cx="573" cy="356" r="1.3"/><circle cx="591" cy="356" r="1.3"/><circle cx="609" cy="356" r="1.3"/><circle cx="627" cy="356" r="1.3"/>
      <circle cx="573" cy="372" r="1.3"/><circle cx="591" cy="372" r="1.3"/><circle cx="609" cy="372" r="1.3"/><circle cx="627" cy="372" r="1.3"/>
      <circle cx="573" cy="388" r="1.3"/><circle cx="591" cy="388" r="1.3"/><circle cx="609" cy="388" r="1.3"/><circle cx="627" cy="388" r="1.3"/>
      <circle cx="573" cy="404" r="1.3"/><circle cx="591" cy="404" r="1.3"/><circle cx="609" cy="404" r="1.3"/><circle cx="627" cy="404" r="1.3"/>
      <circle cx="573" cy="419" r="1.3"/><circle cx="591" cy="419" r="1.3"/><circle cx="609" cy="419" r="1.3"/><circle cx="627" cy="419" r="1.3"/>
    </g>
    <path class="sun-wave" d="M0,900 C150,830 300,720 450,720 C620,720 780,840 893,900 L893,1200 L0,1200 Z" fill="var(--sun)"/>
    <path class="coral-arch" d="M0,984 C110,830 270,723 443,723 C630,723 800,830 893,978 L893,1200 L0,1200 Z" fill="var(--coral)"/>
  </svg>

  <h1 class="headline">YOUR <span class="accent">CAREER</span> IS JUST<span class="second">A CLICK AWAY</span></h1>
  <h2 class="course-title">DESKTOP &amp; NETWORK SUPPORT<br>COURSE</h2>

  <ul class="checklist">
    <li><svg viewBox="0 0 28 28"><path d="M24 11.5A11 11 0 1 1 18.5 4" fill="none" stroke="var(--coral)" stroke-width="2.4" stroke-linecap="round"/><path d="M8.5 13.5l4.5 4.5L25 5" fill="none" stroke="var(--coral)" stroke-width="2.4" stroke-linecap="round" stroke-linejoin="round"/></svg>Master Corvel Operating Systems</li>
    <li><svg viewBox="0 0 28 28"><path d="M24 11.5A11 11 0 1 1 18.5 4" fill="none" stroke="var(--coral)" stroke-width="2.4" stroke-linecap="round"/><path d="M8.5 13.5l4.5 4.5L25 5" fill="none" stroke="var(--coral)" stroke-width="2.4" stroke-linecap="round" stroke-linejoin="round"/></svg>90% Employment Rate – Class of 2024</li>
    <li><svg viewBox="0 0 28 28"><path d="M24 11.5A11 11 0 1 1 18.5 4" fill="none" stroke="var(--coral)" stroke-width="2.4" stroke-linecap="round"/><path d="M8.5 13.5l4.5 4.5L25 5" fill="none" stroke="var(--coral)" stroke-width="2.4" stroke-linecap="round" stroke-linejoin="round"/></svg>Prepare for 3 of the Top 10 Tech Jobs</li>
    <li><svg viewBox="0 0 28 28"><path d="M24 11.5A11 11 0 1 1 18.5 4" fill="none" stroke="var(--coral)" stroke-width="2.4" stroke-linecap="round"/><path d="M8.5 13.5l4.5 4.5L25 5" fill="none" stroke="var(--coral)" stroke-width="2.4" stroke-linecap="round" stroke-linejoin="round"/></svg>National College Review 2025</li>
  </ul>

  <ul class="highlights">
    <li>HANDS-ON DESKTOP &amp; NETWORK TRAINING</li>
    <li>REAL-WORLD TROUBLESHOOTING SKILLS</li>
    <li>READY FOR IT JOBS</li>
  </ul>

  <div class="card card--modes">
    <svg class="icon" viewBox="0 0 48 48"><circle cx="24" cy="24" r="22.5" fill="none" stroke="var(--sun)" stroke-width="1" stroke-dasharray="3 2.5"/><circle cx="24" cy="19" r="4.5" fill="#fff"/><path d="M15 31c0-5 4-7 9-7s9 2 9 7c0 1.5-1 2.5-2.5 2.5h-13C16 33.5 15 32.5 15 31z" fill="#fff"/></svg>
    <p>IN-PERSON AND REMOTE<br>OPTIONS</p>
  </div>

  <div class="card card--aid">
    <svg class="icon" viewBox="0 0 48 48"><circle cx="24" cy="24" r="22.5" fill="none" stroke="var(--sun)" stroke-width="1" stroke-dasharray="3 2.5"/><path d="M13 21l11-5 11 5-11 5z" fill="#fff"/><path d="M17 23.5v5.5c2 2 12 2 14 0v-5.5l-7 3.2z" fill="#fff"/><path d="M14 21.5v6" stroke="#fff" stroke-width="1.5"/></svg>
    <p>PARTIAL SCHOLARSHIPS<br>OFFERED</p>
  </div>
</div>
</body>
</html>
```